House-share and Room Rental Website (With Focus on the Bedroom Landing Page)

Looking for website design for our House-share (executive accommodation) and room rental business.

Our company name is: Lodgivo could also be written as LodGivo or lodgivo. Either is fine .. just looking for a nice clean catchy logo to go with the design.

EXAMPLES
These are examples of other websites in this field that are doing well. this is a kind of baseline.
https://nestpartners-example.com.au/
https://www.bunkora-example.com/
https://www.dwelzy-example.com/
https://www.habiquo-example.net/
https://www.cohabiscout-example.com.au/

Our business model is to rent rooms to people looking for high-quality accommodation. We fill the gap between those looking to rent rooms and those with rooms to rent. However, our model is slightly different from those already on the market as we looking to fill a massive gap in the market delivering upmarket rooms for rent.(Executive Accommodation) also in the back end will be coupled with a self management process in the back end.

We offer executive style accommodation that stands out above the rest. With special extras like fire safety.. and management processes that create happier homes. We are looking for a web design package that can help us grow and scale our business. We need a design that is captivating

Our MAIN focus is having a room landing page that stands out from the rest... The core of our business will rely on the promotion of the rooms in a share house... so the whole design relies on the BEDROOM landing page to drive results.

Target Market(s)

We have 2 markets we are aiming at ... the first market is people offering rooms to rent who want the highest rental return. The second market is people looking to rent safe, high-quality rooms, in houses that are well managed and looked after.

Industry/Entity Type

Share Economy

Logo Text

LodGivo

Number of Pages Required

5+ page

Font styles to use
Sans Serif

Colors
3276b5

Requirements
Must have
• A messaging system whereby we can create direct communication between those offering rooms and those looking for rooms.
• A call to action that says " Schedule an Inspection"
• Landing page for promoting rooms
• A home page for showing stock.
• Profile page for those selling rooms
• Profile page for those looking for rooms.
• A scheduling calendar for booking inspections
Nice to have
• Pages where new residents can lock in a room.. pay bond and rents.. and sign contracts
• Notifications
• SMS capabilities in the backend.
Should not have
• No script or handwriting fonts.

```html
<!DOCTYPE html>
<html lang="en">
<head>
<meta charset="utf-8">
<title>Lodgivo – Executive Accommodation</title>
<link rel="stylesheet" href="https://fonts.googleapis.com/css2?family=Raleway:wght@500;600;700&family=Lato:wght@400;700&display=swap">
<style>
:root{
  --blue:#1a74c4;
  --ink:#222;
  --line:#d9dde2;
  --page:#f6f6f6;
  --card:#fff;
  --footer:#262626;
  --footer-ink:#e8e8e8;
  --btn-dark:#3b3b3b;
}
*{box-sizing:border-box;margin:0;padding:0}
html,body{width:1200px;height:3364px;overflow:hidden}
body{position:relative;background:var(--page);font-family:"Lato",Arial,sans-serif;color:var(--ink)}
.abs{position:absolute}
.heading{font-family:"Raleway",Arial,sans-serif;font-weight:600;color:var(--ink);text-align:center;width:1200px;left:0}

/* header */
.site-header{position:absolute;left:0;top:0;width:1200px;height:99px;background:#fff}
.menu-grid{left:78px;top:38px}
.lang{left:120px;top:38px;font-size:12px;color:#333;display:flex;align-items:center;gap:6px}
.lang .flag{width:16px;height:11px;background:linear-gradient(#b22 0 50%,#fff 50%);border:1px solid #ccc}
.brand{left:0;top:24px;width:1200px;text-align:center}
.brand-name{font-family:"Lato",sans-serif;font-weight:700;font-size:30px;color:var(--blue);line-height:1;display:block}
.brand-tag{font-family:"Lato",sans-serif;font-size:11px;color:#333;display:block;margin-top:3px}
.btn-post{left:918px;top:32px;width:128px;height:30px;background:var(--blue);color:#fff;border-radius:4px;font-size:12px;display:flex;align-items:center;justify-content:center}
.btn-login{left:1055px;top:32px;width:63px;height:30px;border:1px solid #999;border-radius:4px;font-size:12px;display:flex;align-items:center;justify-content:center;color:#333}

/* hero */
.hero{left:0;top:99px;width:1200px;height:554px;background:linear-gradient(120deg,#3a2a1e 0%,#7a5636 35%,#a77c53 55%,#4a3424 80%,#2a1e16 100%)}
.hero-title{left:224px;top:248px;font-family:"Raleway",sans-serif;font-size:32px;font-weight:500;color:#fff;line-height:1.25}
.hero-arrow{top:262px;color:#fff;font-size:26px}
.search-card{left:787px;top:101px;width:332px;height:367px;background:#fff;border-radius:6px;box-shadow:0 4px 14px rgba(0,0,0,.25)}
.search-card h2{font-family:"Raleway",sans-serif;font-size:18px;font-weight:600;position:absolute;left:45px;top:22px}
.field-label{position:absolute;font-size:11px;color:#333}
.field{position:absolute;height:32px;border:1px solid var(--line);border-radius:4px;font-size:11px;color:#333;padding:0 12px;display:flex;align-items:center;justify-content:space-between}
.btn-search{position:absolute;left:25px;top:309px;width:282px;height:34px;background:var(--blue);color:#fff;border-radius:4px;font-size:12px;display:flex;align-items:center;justify-content:center}

/* amenities */
.amenity{position:absolute;top:785px;width:200px;text-align:center}
.amenity .icon{width:82px;height:82px;border-radius:50%;background:var(--blue);margin:0 auto;display:flex;align-items:center;justify-content:center}
.amenity h3{font-family:"Lato",sans-serif;font-weight:400;font-size:19px;margin-top:18px}
.amenity p{font-size:12px;line-height:1.35;color:#333;margin:16px auto 0;width:165px}
.amenity .go{display:block;margin:14px auto 0;width:24px;height:24px}

/* tabs */
.tab{position:absolute;top:1150px;width:100px;text-align:center;font-family:"Raleway",sans-serif;font-size:18px;color:#333}
.tab svg{display:block;margin:0 auto 8px}
.tab.active{color:var(--blue)}

/* room cards */
.room{position:absolute;width:325px;height:415px;background:#fff;box-shadow:0 1px 6px rgba(0,0,0,.12)}
.room .photo{position:absolute;left:0;top:0;width:325px;height:213px}
.room .check{position:absolute;left:8px;top:8px;width:18px;height:18px;border:2px solid #fff;background:rgba(255,255,255,.15)}
.room .price{position:absolute;left:0;top:160px;height:36px;padding:0 14px 0 10px;background:var(--blue);color:#fff;font-weight:700;font-size:20px;display:flex;align-items:center;clip-path:polygon(0 0,88% 0,100% 50%,88% 100%,0 100%)}
.room h4{position:absolute;left:18px;top:229px;font-family:"Raleway",sans-serif;font-weight:600;font-size:15px;color:var(--blue)}
.room .addr{position:absolute;left:16px;top:274px;font-size:13px;color:#444;display:flex;align-items:center;gap:8px;white-space:nowrap}
.room .specs{position:absolute;left:0;top:308px;width:325px;display:flex;justify-content:space-around;font-size:11px;color:#444;text-align:center}
.room .specs div{width:90px}
.room .specs b{display:flex;align-items:center;justify-content:center;gap:6px;font-weight:400;font-size:12px;margin-bottom:8px}
.room .browse{position:absolute;left:96px;top:370px;width:132px;height:28px;background:var(--btn-dark);color:#fff;border-radius:4px;font-size:11px;display:flex;align-items:center;justify-content:center}
.btn-more{left:538px;top:2213px;width:128px;height:30px;background:var(--blue);color:#fff;border-radius:4px;font-size:12px;display:flex;align-items:center;justify-content:center}

/* testimonials */
.quote{position:absolute;top:2405px;width:293px;height:289px;background:#fff;text-align:center}
.quote .avatar{width:100px;height:100px;border-radius:50%;margin:30px auto 0;background:linear-gradient(160deg,#6c6058,#b9a597)}
.quote h5{font-family:"Lato",sans-serif;font-weight:700;font-size:17px;margin-top:12px}
.quote .role{font-size:12px;color:var(--blue);margin-top:3px}
.quote p{font-size:12px;line-height:1.4;margin:14px auto 0;width:200px;color:#333}
.quote .more{font-size:13px;color:#333;margin-top:14px;display:flex;align-items:center;justify-content:center;gap:5px}

/* newsletter */
.news-input{left:336px;top:2858px;width:570px;height:38px;background:#fff;border:1px solid #eee;font-size:12px;color:#888;padding-left:16px;display:flex;align-items:center}
.news-btn{left:772px;top:2858px;width:134px;height:38px;background:var(--blue);color:#fff;font-size:14px;display:flex;align-items:center;justify-content:center}

/* footer */
.site-footer{left:0;top:2954px;width:1200px;height:352px;background:var(--footer);color:var(--footer-ink)}
.f-brand{left:79px;top:74px}
.f-brand .brand-name{font-size:28px}
.f-brand .brand-tag{color:#fff}
.f-about{left:79px;top:146px;width:230px;font-size:13px;line-height:1.6}
.socials{left:79px;top:254px;display:flex;gap:9px}
.socials span{width:22px;height:22px;border-radius:50%;border:1.5px solid #ddd}
.socials span:first-child{background:var(--blue);border-color:var(--blue)}
.f-title{position:absolute;top:80px;font-size:15px;color:#fff;font-weight:400}
.f-links{left:372px;top:142px;list-style:none;font-size:11px;line-height:24px}
.f-links li::before{content:"›";margin-right:14px;font-size:14px}
.f-contact{left:576px;top:142px;font-size:13px;line-height:1.75}
.f-contact .row{display:flex;gap:12px;margin-bottom:10px}
.q-field{position:absolute;background:#3a3a3a;border:1px solid #4a4a4a;font-size:12px;color:#ddd;padding:6px 10px}
.q-send{left:994px;top:250px;width:125px;height:28px;background:var(--blue);color:#fff;font-size:12px;border-radius:3px;display:flex;align-items:center;justify-content:center}
.bottom-bar{left:0;top:3306px;width:1200px;height:58px;background:var(--blue);color:#fff;font-size:12px}
.bottom-bar .copy{position:absolute;left:79px;top:21px}
.pay{position:absolute;top:18px;display:flex;gap:10px;left:915px}
.pay span{width:34px;height:22px;background:#fff;border-radius:3px}
</style>
</head>
<body>

<header class="site-header">
  <svg class="abs menu-grid" width="24" height="24" viewBox="0 0 24 24" fill="#444"><rect x="0" y="0" width="6" height="6"/><rect x="9" y="0" width="6" height="6"/><rect x="18" y="0" width="6" height="6"/><rect x="0" y="9" width="6" height="6"/><rect x="9" y="9" width="6" height="6"/><rect x="18" y="9" width="6" height="6"/><rect x="0" y="18" width="6" height="6"/><rect x="9" y="18" width="6" height="6"/><rect x="18" y="18" width="6" height="6"/></svg>
  <div class="abs lang"><span class="flag"></span>Eng ▾</div>
  <div class="abs brand"><span class="brand-name">Lodgivo</span><span class="brand-tag">Executive Accommodation</span></div>
  <div class="abs btn-post">Post Your Room</div>
  <div class="abs btn-login">Log in</div>
</header>

<section class="abs hero" role="img" aria-label="Photo of an upscale hotel-style bedroom with two beds and wood panelling">
  <div class="abs hero-arrow" style="left:30px">‹</div>
  <div class="abs hero-arrow" style="left:1148px">›</div>
  <h1 class="abs hero-title">Let us Find Your Perfect<br>Room For Rent</h1>
  <form class="abs search-card" aria-label="Find your room">
    <h2>Find Your Room For Rent</h2>
    <span class="field-label" style="left:25px;top:58px">Where</span>
    <div class="field" style="left:25px;top:74px;width:282px">Anywhere
      <svg width="12" height="14" viewBox="0 0 12 14"><path d="M6 13C6 13 1 8 1 5a5 5 0 0 1 10 0c0 3-5 8-5 8z" fill="none" stroke="#888"/><circle cx="6" cy="5" r="1.8" fill="#888"/></svg></div>
    <span class="field-label" style="left:25px;top:125px">Check in</span>
    <span class="field-label" style="left:175px;top:125px">Check out</span>
    <div class="field" style="left:25px;top:142px;width:132px;height:38px;justify-content:flex-end"><svg width="14" height="14" viewBox="0 0 14 14" fill="none" stroke="#888"><rect x="1" y="2" width="12" height="11"/><path d="M1 5h12M4 0v3M10 0v3"/></svg></div>
    <div class="field" style="left:175px;top:142px;width:132px;height:38px;justify-content:flex-end"><svg width="14" height="14" viewBox="0 0 14 14" fill="none" stroke="#888"><rect x="1" y="2" width="12" height="11"/><path d="M1 5h12M4 0v3M10 0v3"/></svg></div>
    <span class="field-label" style="left:25px;top:193px">Category</span>
    <div class="field" style="left:25px;top:209px;width:282px">Room For Rent<span>▾</span></div>
    <div class="field" style="left:25px;top:257px;width:282px">Guests<span>▾</span></div>
    <div class="btn-search">Search</div>
  </form>
</section>

<h2 class="abs heading" style="top:708px;font-size:31px">Public Amenities</h2>

<div class="amenity" style="left:61px">
  <div class="icon"><svg width="44" height="44" viewBox="0 0 44 44" fill="#fff"><path d="M8 24l4-10h20l4 10v10h-5v-4H13v4H8z"/><rect x="13" y="17" width="18" height="6" fill="#1a74c4"/><circle cx="13" cy="27" r="2" fill="#1a74c4"/><circle cx="31" cy="27" r="2" fill="#1a74c4"/></svg></div>
  <h3>Transport</h3><p>Lorem Ipsum is simply is a text of the printinghas been ndustry's 1500s...</p>
  <svg class="go" viewBox="0 0 24 24" fill="none" stroke="#333" stroke-width="1.6"><circle cx="12" cy="12" r="10"/><path d="M7 12h10M13 8l4 4-4 4"/></svg>
</div>
<div class="amenity" style="left:288px">
  <div class="icon"><svg width="44" height="44" viewBox="0 0 44 44" fill="#fff"><rect x="11" y="6" width="22" height="26" rx="4"/><rect x="14" y="10" width="16" height="9" fill="#1a74c4"/><circle cx="16" cy="26" r="2" fill="#1a74c4"/><circle cx="28" cy="26" r="2" fill="#1a74c4"/><path d="M13 38l4-6h2l-4 6zM31 38l-4-6h-2l4 6z"/></svg></div>
  <h3>Trains</h3><p>Lorem Ipsum is simply is a text of the printinghas been ndustry's 1500s...</p>
  <svg class="go" viewBox="0 0 24 24" fill="none" stroke="#333" stroke-width="1.6"><circle cx="12" cy="12" r="10"/><path d="M7 12h10M13 8l4 4-4 4"/></svg>
</div>
<div class="amenity" style="left:501px">
  <div class="icon"><svg width="44" height="44" viewBox="0 0 44 44" fill="#fff"><rect x="10" y="6" width="24" height="28" rx="4"/><rect x="13" y="11" width="18" height="10" fill="#1a74c4"/><circle cx="16" cy="28" r="2" fill="#1a74c4"/><circle cx="28" cy="28" r="2" fill="#1a74c4"/><rect x="12" y="34" width="4" height="4"/><rect x="28" y="34" width="4" height="4"/></svg></div>
  <h3>Busses</h3><p>Lorem Ipsum is simply is a text of the printinghas been ndustry's 1500s...</p>
  <svg class="go" viewBox="0 0 24 24" fill="none" stroke="#333" stroke-width="1.6"><circle cx="12" cy="12" r="10"/><path d="M7 12h10M13 8l4 4-4 4"/></svg>
</div>
<div class="amenity" style="left:716px">
  <div class="icon"><svg width="44" height="44" viewBox="0 0 44 44" fill="#fff"><path d="M22 38S12 26 12 18a10 10 0 0 1 20 0c0 8-10 20-10 20z"/><circle cx="22" cy="18" r="4" fill="#1a74c4"/></svg></div>
  <h3>Location</h3><p>Lorem Ipsum is simply is a text of the printinghas been ndustry's 1500s...</p>
  <svg class="go" viewBox="0 0 24 24" fill="none" stroke="#333" stroke-width="1.6"><circle cx="12" cy="12" r="10"/><path d="M7 12h10M13 8l4 4-4 4"/></svg>
</div>
<div class="amenity" style="left:936px">
  <div class="icon"><svg width="44" height="44" viewBox="0 0 44 44" fill="none" stroke="#fff" stroke-width="2.5"><path d="M8 11l9-3 10 3 9-3v25l-9 3-10-3-9 3z"/><path d="M17 8v25M27 11v25"/></svg></div>
  <h3>MAP</h3><p>Lorem Ipsum is simply is a text of the printinghas been ndustry's 1500s...</p>
  <svg class="go" viewBox="0 0 24 24" fill="none" stroke="#333" stroke-width="1.6"><circle cx="12" cy="12" r="10"/><path d="M7 12h10M13 8l4 4-4 4"/></svg>
</div>

<h2 class="abs heading" style="top:1075px;font-size:31px">Recommended for you</h2>

<div class="tab" style="left:257px"><svg width="38" height="38" viewBox="0 0 38 38" fill="#333"><rect x="2" y="2" width="9" height="9"/><rect x="14" y="2" width="9" height="9"/><rect x="26" y="2" width="9" height="9"/><rect x="2" y="14" width="9" height="9"/><rect x="14" y="14" width="9" height="9"/><rect x="26" y="14" width="9" height="9"/><rect x="2" y="26" width="9" height="9"/><rect x="14" y="26" width="9" height="9"/><rect x="26" y="26" width="9" height="9"/></svg>All</div>
<div class="tab active" style="left:405px"><svg width="38" height="38" viewBox="0 0 38 38" fill="none" stroke="#1a74c4" stroke-width="3"><rect x="9" y="2" width="20" height="34"/><circle cx="23" cy="20" r="1.8" fill="#1a74c4"/></svg>Room</div>
<div class="tab" style="left:549px"><svg width="44" height="38" viewBox="0 0 44 40" fill="#333"><path d="M22 2L2 20h6v18h11V27h6v11h11V20h6z"/></svg>House</div>
<div class="tab" style="left:701px"><svg width="48" height="38" viewBox="0 0 48 40" fill="none" stroke="#333" stroke-width="2.5"><rect x="3" y="6" width="42" height="10"/><rect x="3" y="22" width="42" height="10"/><path d="M3 2v36M45 2v36"/><rect x="8" y="9" width="8" height="5" fill="#333"/><rect x="8" y="25" width="8" height="5" fill="#333"/></svg>Roomate</div>
<div class="tab" style="left:849px"><svg width="40" height="38" viewBox="0 0 40 40" fill="#333"><path d="M20 2L2 18h5v20h26V18h5z"/><circle cx="20" cy="20" r="4" fill="#fff"/><path d="M13 34c0-5 3-8 7-8s7 3 7 8z" fill="#fff"/></svg>Tenant</div>

<article class="room" style="left:81px;top:1276px">
  <div class="photo" role="img" aria-label="Photo of a timber-framed bedroom with a patterned bed" style="background:linear-gradient(135deg,#5a3620,#a86e3f 50%,#3c2414)"></div>
  <span class="check"></span><span class="price">$250</span>
  <h4>Luxurious &amp; Stunning Room</h4>
  <div class="addr"><svg width="12" height="15" viewBox="0 0 12 15"><path d="M6 14S1 9 1 5.5a5 5 0 0 1 10 0C11 9 6 14 6 14z" fill="none" stroke="#555" stroke-width="1.3"/><circle cx="6" cy="5.5" r="1.7" fill="#555"/></svg>18 Harbourline Road, Ellmere, Australia</div>
  <div class="specs"><div><b>▣ 2</b>Rooms</div><div><b>▭ 4</b>Bedrooms</div><div><b>⌂ 2</b>Bath</div></div>
  <div class="browse">Browse</div>
</article>
<article class="room" style="left:435px;top:1276px">
  <div class="photo" role="img" aria-label="Photo of a bright classic bedroom with a bay window" style="background:linear-gradient(135deg,#c8b08a,#8f6b48 55%,#4b3022)"></div>
  <span class="check"></span><span class="price">$250</span>
  <h4>Luxurious &amp; Stunning Room</h4>
  <div class="addr"><svg width="12" height="15" viewBox="0 0 12 15"><path d="M6 14S1 9 1 5.5a5 5 0 0 1 10 0C11 9 6 14 6 14z" fill="none" stroke="#555" stroke-width="1.3"/><circle cx="6" cy="5.5" r="1.7" fill="#555"/></svg>18 Harbourline Road, Ellmere, Australia</div>
  <div class="specs"><div><b>▣ 2</b>Rooms</div><div><b>▭ 4</b>Bedrooms</div><div><b>⌂ 2</b>Bath</div></div>
  <div class="browse">Browse</div>
</article>
<article class="room" style="left:794px;top:1276px">
  <div class="photo" role="img" aria-label="Photo of a modern hotel bedroom with red accents" style="background:linear-gradient(135deg,#b8a068,#6d5032 50%,#8a2a2a)"></div>
  <span class="check"></span><span class="price">$250</span>
  <h4>Luxurious &amp; Stunning Room</h4>
  <div class="addr"><svg width="12" height="15" viewBox="0 0 12 15"><path d="M6 14S1 9 1 5.5a5 5 0 0 1 10 0C11 9 6 14 6 14z" fill="none" stroke="#555" stroke-width="1.3"/><circle cx="6" cy="5.5" r="1.7" fill="#555"/></svg>18 Harbourline Road, Ellmere, Australia</div>
  <div class="specs"><div><b>▣ 2</b>Rooms</div><div><b>▭ 4</b>Bedrooms</div><div><b>⌂ 2</b>Bath</div></div>
  <div class="browse">Browse</div>
</article>
<article class="room" style="left:81px;top:1738px">
  <div class="photo" role="img" aria-label="Photo of a bedroom with dark wooden furniture and warm walls" style="background:linear-gradient(135deg,#9a5a2a,#5b3a22 50%,#c7a46a)"></div>
  <span class="check"></span><span class="price">$250</span>
  <h4>Luxurious &amp; Stunning Room</h4>
  <div class="addr"><svg width="12" height="15" viewBox="0 0 12 15"><path d="M6 14S1 9 1 5.5a5 5 0 0 1 10 0C11 9 6 14 6 14z" fill="none" stroke="#555" stroke-width="1.3"/><circle cx="6" cy="5.5" r="1.7" fill="#555"/></svg>18 Harbourline Road, Ellmere, Australia</div>
  <div class="specs"><div><b>▣ 2</b>Rooms</div><div><b>▭ 4</b>Bedrooms</div><div><b>⌂ 2</b>Bath</div></div>
  <div class="browse">Browse</div>
</article>
<article class="room" style="left:435px;top:1738px">
  <div class="photo" role="img" aria-label="Photo of a dim bedroom with a four-poster bed" style="background:linear-gradient(135deg,#3a2618,#7a5a3a 50%,#d8c4a0)"></div>
  <span class="check"></span><span class="price">$250</span>
  <h4>Luxurious &amp; Stunning Room</h4>
  <div class="addr"><svg width="12" height="15" viewBox="0 0 12 15"><path d="M6 14S1 9 1 5.5a5 5 0 0 1 10 0C11 9 6 14 6 14z" fill="none" stroke="#555" stroke-width="1.3"/><circle cx="6" cy="5.5" r="1.7" fill="#555"/></svg>18 Harbourline Road, Ellmere, Australia</div>
  <div class="specs"><div><b>▣ 2</b>Rooms</div><div><b>▭ 4</b>Bedrooms</div><div><b>⌂ 2</b>Bath</div></div>
  <div class="browse">Browse</div>
</article>
<article class="room" style="left:794px;top:1738px">
  <div class="photo" role="img" aria-label="Photo of an ornate bedroom with deep red walls" style="background:linear-gradient(135deg,#7a2020,#b44a3a 50%,#e0d0c0)"></div>
  <span class="check"></span><span class="price">$250</span>
  <h4>Luxurious &amp; Stunning Room</h4>
  <div class="addr"><svg width="12" height="15" viewBox="0 0 12 15"><path d="M6 14S1 9 1 5.5a5 5 0 0 1 10 0C11 9 6 14 6 14z" fill="none" stroke="#555" stroke-width="1.3"/><circle cx="6" cy="5.5" r="1.7" fill="#555"/></svg>18 Harbourline Road, Ellmere, Australia</div>
  <div class="specs"><div><b>▣ 2</b>Rooms</div><div><b>▭ 4</b>Bedrooms</div><div><b>⌂ 2</b>Bath</div></div>
  <div class="browse">Browse</div>
</article>

<div class="abs btn-more">View More</div>

<p class="abs heading" style="top:2305px;font-size:13px;font-family:'Lato',sans-serif;font-weight:400">Testimonials</p>
<h2 class="abs heading" style="top:2333px;font-size:31px;font-weight:500">What Client Say</h2>

<div class="quote" style="left:119px"><div class="avatar" role="img" aria-label="Portrait photo of the client"></div><h5>Marcus</h5><div class="role">Director</div><p>Lorem Ipsum is simply dummy of the printing and typesetting Lorem Ipsum industry.</p><div class="more">Read More... <svg width="14" height="14" viewBox="0 0 24 24" fill="none" stroke="#333" stroke-width="2"><circle cx="12" cy="12" r="10"/><path d="M7 12h10M13 8l4 4-4 4"/></svg></div></div>
<div class="quote" style="left:453px"><div class="avatar" role="img" aria-label="Portrait photo of the client" style="background:linear-gradient(160deg,#3f6f9a,#c9a68a)"></div><h5>Elliot</h5><div class="role">Director</div><p>Lorem Ipsum is simply dummy of the printing and typesetting Lorem Ipsum industry.</p><div class="more">Read More... <svg width="14" height="14" viewBox="0 0 24 24" fill="none" stroke="#333" stroke-width="2"><circle cx="12" cy="12" r="10"/><path d="M7 12h10M13 8l4 4-4 4"/></svg></div></div>
<div class="quote" style="left:783px"><div class="avatar" role="img" aria-label="Portrait photo of the client" style="background:linear-gradient(160deg,#2a2a2a,#a88a70)"></div><h5>Rafael</h5><div class="role">Director</div><p>Lorem Ipsum is simply dummy of the printing and typesetting Lorem Ipsum industry.</p><div class="more">Read More... <svg width="14" height="14" viewBox="0 0 24 24" fill="none" stroke="#333" stroke-width="2"><circle cx="12" cy="12" r="10"/><path d="M7 12h10M13 8l4 4-4 4"/></svg></div></div>

<h2 class="abs heading" style="top:2772px;font-size:25px;font-weight:500">Subscribe To Our Newsletter</h2>
<p class="abs heading" style="top:2814px;font-size:12px;font-family:'Lato',sans-serif;font-weight:400">To Receive The latest News And Update</p>
<div class="abs news-input">Your E-Mail</div>
<div class="abs news-btn">Submit</div>

<footer class="abs site-footer">
  <div class="abs f-brand"><span class="brand-name">Lodgivo</span><span class="brand-tag">Executive Accommodation</span></div>
  <p class="abs f-about">Lorem Ipsum is simply dummy text of the printing and types tysietting industry... ⊕</p>
  <div class="abs socials"><span></span><span></span><span></span><span></span><span></span><span></span></div>

  <h6 class="f-title" style="left:372px">Useful links</h6>
  <ul class="abs f-links"><li>Login</li><li>Register</li><li>My Profile</li><li>My Subscription</li><li>Privacy policy</li><li>Terms &amp; Conditions</li></ul>

  <h6 class="f-title" style="left:576px">Contact us</h6>
  <div class="abs f-contact">
    <div class="row"><svg width="16" height="16" viewBox="0 0 16 16" fill="#ddd"><path d="M8 1L1 7h2v7h4v-4h2v4h4V7h2z"/></svg><span>27 Wattlebrook Place, Kelvara<br>Western Australia.<br>ZipCode: 12345</span></div>
    <div class="row"><svg width="16" height="16" viewBox="0 0 16 16" fill="#ddd"><path d="M3 1h3l1 4-2 1a9 9 0 0 0 5 5l1-2 4 1v3c0 1-1 2-2 2A13 13 0 0 1 1 3c0-1 1-2 2-2z"/></svg><span>555 014 2290</span></div>
    <div class="row"><svg width="16" height="16" viewBox="0 0 16 16" fill="none" stroke="#ddd" stroke-width="1.5"><rect x="1" y="3" width="14" height="10"/><path d="M1 3l7 6 7-6"/></svg><span>info@lodgivo.com</span></div>
  </div>

  <h6 class="f-title" style="left:890px">Quick Contact</h6>
  <div class="q-field" style="left:890px;top:146px;width:113px;height:26px">Name</div>
  <div class="q-field" style="left:1008px;top:146px;width:111px;height:26px">Phone</div>
  <div class="q-field" style="left:890px;top:179px;width:229px;height:63px">Message</div>
  <div class="abs q-send">Send</div>
</footer>

<div class="abs bottom-bar">
  <span class="copy">CopyRight © 2019 Lodgivo. All Right Reserve</span>
  <div class="pay"><span></span><span></span><span></span><span></span><span></span></div>
</div>

</body>
</html>
```